Kestrel Hearth Business Card Design

Design new, 2 sides, business cards for a residential and light commercial heating, air conditioning contractor.

Target Market(s)

Homeowners, small businesses

Industry/Entity Type

Business

Contact Information for Business Card

Dominic Westerhall
Phone - 862-415-2736
Email
Address - PO box 518
Brightwater NJ 07912
Website - www.HarborBreezeLLC.example

Requirements
Must have
• logo, company colors, standard size with no die cut, so I can use nova stamp

```html
<!DOCTYPE html>
<html lang="en">
<head>
<meta charset="utf-8">
<title>Kestrel Hearth Business Card</title>
<link href="https://fonts.googleapis.com/css2?family=Roboto:wght@400;700&display=swap" rel="stylesheet">
<style>
  :root {
    --backdrop: #e9e6e1;
    --card-white: #ffffff;
    --brand-red: #9c1f36;
    --brand-orange: #f08a24;
    --brand-yellow: #f6c43c;
    --text-light: #f7eef0;
  }
  * { box-sizing: border-box; margin: 0; padding: 0; }
  html, body { width: 1200px; height: 950px; overflow: hidden; }
  body {
    background: var(--backdrop);
    font-family: "Roboto", Arial, sans-serif;
    display: flex;
    flex-direction: column;
    align-items: center;
    justify-content: center;
    gap: 60px;
  }
  .card {
    width: 630px;
    height: 360px;
    position: relative;
    box-shadow: 0 6px 18px rgba(0,0,0,0.18);
  }
  .card--front { background: var(--card-white); }
  .card--back { background: var(--brand-red); color: var(--text-light); }

  .brand-mark {
    position: absolute;
    right: 40px;
    bottom: 34px;
    display: flex;
    align-items: center;
    gap: 10px;
  }
  .brand-mark__dot {
    width: 22px; height: 22px;
    border-radius: 50%;
    background: var(--brand-orange);
  }
  .brand-mark__name {
    font-weight: 700;
    font-size: 30px;
    line-height: 1;
    text-transform: uppercase;
    letter-spacing: 1px;
  }
  .card--front .brand-mark__name { color: var(--brand-red); }
  .card--back .brand-mark__name { color: var(--brand-yellow); }

  .holder {
    position: absolute;
    left: 44px;
    top: 40px;
  }
  .holder__name {
    font-weight: 700;
    font-size: 20px;
    letter-spacing: 0.5px;
    text-transform: uppercase;
    color: var(--text-light);
  }
  .holder__title {
    font-size: 14px;
    text-transform: uppercase;
    color: var(--brand-orange);
    margin-top: 3px;
  }
  .address {
    position: absolute;
    left: 44px;
    top: 120px;
    font-size: 14px;
    line-height: 19px;
  }
  .contact-list {
    position: absolute;
    left: 44px;
    top: 172px;
    list-style: none;
    font-size: 14px;
  }
  .contact-list li {
    display: flex;
    align-items: center;
    gap: 9px;
    height: 20px;
  }
  .contact-icon {
    width: 15px; height: 15px;
    border-radius: 50%;
    background: var(--brand-yellow);
    display: flex;
    align-items: center;
    justify-content: center;
  }
  .contact-icon svg { width: 9px; height: 9px; fill: var(--brand-red); }
</style>
</head>
<body>
  <section class="card card--front" aria-label="Card front">
    <div class="brand-mark">
      <span class="brand-mark__dot"></span>
      <span class="brand-mark__name">Kestrel Hearth</span>
    </div>
  </section>

  <section class="card card--back" aria-label="Card back">
    <div class="holder">
      <p class="holder__name">Dominic Westerhall</p>
      <p class="holder__title">President</p>
    </div>
    <p class="address">PO box 518<br>Brightwater NJ 07912</p>
    <ul class="contact-list">
      <li><span class="contact-icon"><svg viewBox="0 0 10 10"><path d="M2 0.5 L3.6 0.5 L4.2 2.8 L3 3.6 Q4 5.8 6.4 7 L7.2 5.8 L9.5 6.4 L9.5 8 Q9.5 9.5 8 9.5 Q0.5 9 0.5 2 Q0.5 0.5 2 0.5Z"/></svg></span>862-415-2736</li>
      <li><span class="contact-icon"><svg viewBox="0 0 10 10"><rect x="2.5" y="0.5" width="5" height="9" rx="1"/></svg></span>862-415-2741</li>
      <li><span class="contact-icon"><svg viewBox="0 0 10 10"><rect x="1" y="3" width="8" height="6"/><rect x="2.5" y="0.5" width="5" height="3"/></svg></span>862-415-2759</li>
      <li><span class="contact-icon"><svg viewBox="0 0 10 10"><path d="M0.5 2 H9.5 V8.5 H0.5Z M0.5 2 L5 5.5 L9.5 2" stroke="#9c1f36" stroke-width="0.6" fill="none"/></svg></span>dominic@kestrelhearth.example</li>
      <li><span class="contact-icon"><svg viewBox="0 0 10 10"><circle cx="5" cy="5" r="4.2" fill="none" stroke="#9c1f36" stroke-width="1"/><path d="M1 5 H9 M5 1 V9" stroke="#9c1f36" stroke-width="0.8"/></svg></span>www.KestrelHearthLLC.example</li>
    </ul>
    <div class="brand-mark">
      <span class="brand-mark__dot"></span>
      <span class="brand-mark__name">Kestrel Hearth</span>
    </div>
  </section>
</body>
</html>
```